Create a premium soap bar box bar design for an all-natural, men's skincare brand.

We are launching a men’s premium, natural soap bar and skincare business. To start, we will be launching cold-press, all-natural soap bars with a few additional products such as lotions. We plan to expand our line into additional skincare products such as face exfoliants, moisturizers and cleansers that target basic needs such as anti-aging, clarifying and hydrating.

Our target audience is men ages 25-50, with a secondary audience of male teens. Our target audience are mid to high income, professionals that live in more urban areas, but enjoy being active outdoors after work and on the weekends. Our target audience are hard workers, humble and want to enjoy all that life has to offer – whether that’s on top of a mountain or an ocean wave. They hike, bike, skateboard, surf or any other sport that gets them outside. They are husbands, brothers and fathers – there for their family and friends.

Our brand is sophisticated, adventurous and has a sense of humor. Many of our competitors either focus on the rugged outdoors or are more pretentious. We are in-between. We are free spirited and love the fresh air. Our products are trustworthy with no toxic chemicals or harsh ingredients. We are all-natural and provide high-quality, premium products that our audience expects and deserves.

Target Market(s)

Men, ages 25-54 who are high-earning professionals, yet enjoy getting outdoors and being active on the weekends - hiking, biking, surfing, skateboarding and more.

Industry/Entity Type

Men's skincare

Font styles to use
Sans Serif

Requirements
Must have
• See attachments
Nice to have
• We would prefer to a have a premium, slightly more modern looking design that will appeal to our target audience and slightly higher price point.
Should not have
• Please do not include an icon for the fragrance, i.e. cinnamon sticks. However, we do need some differentiation for the fragrance, i.e. color, etc. as it will be on the shelf with other fragrances.

```html
<!DOCTYPE html>
<html lang="en">
<head>
<meta charset="utf-8">
<title>Rowan Hale – Cinnamon Bark Soap Box</title>
<link rel="stylesheet" href="https://fonts.googleapis.com/css2?family=Montserrat:wght@400;500;600;700;800&display=swap">
<style>
  :root {
    --backdrop: #e6e7e9;
    --kraft: #cfbb9f;
    --kraft-shade: #c3ae91;
    --kraft-end: #c8b497;
    --navy: #12294a;
    --ember: #e8563a;
    --ink: #1b2230;
    --cream: #f3ead9;
  }
  * { box-sizing: border-box; margin: 0; padding: 0; }
  html, body { width: 1200px; height: 857px; overflow: hidden; }
  body {
    background: var(--backdrop);
    font-family: "Montserrat", sans-serif;
    color: var(--navy);
    position: relative;
  }
  .box-layout {
    position: absolute;
    left: 145px; top: 140px;
    width: 910px; height: 580px;
  }

  /* left end panel */
  .end-panel {
    position: absolute; left: 0; top: 0;
    width: 150px; height: 440px;
    background: var(--kraft-end);
    border-right: 1px solid rgba(18,41,74,0.25);
    display: flex; align-items: center; justify-content: center;
  }
  .end-brand {
    display: flex; align-items: center; gap: 14px;
    transform: rotate(90deg);
    white-space: nowrap;
  }
  .end-brand .dot {
    width: 34px; height: 34px; border-radius: 50%;
    border: 3px solid var(--navy); flex: none;
  }
  .end-brand .brand-name { font-size: 30px; }

  /* top face */
  .top-panel {
    position: absolute; left: 150px; top: 0;
    width: 760px; height: 440px;
    background: var(--kraft);
  }
  .front-panel {
    position: absolute; left: 150px; top: 440px;
    width: 760px; height: 140px;
    background: var(--kraft-shade);
    border-top: 1px solid rgba(18,41,74,0.25);
    padding: 26px 40px;
    color: var(--ink);
    font-size: 14px;
    line-height: 1.4;
  }
  .front-panel .lead { font-weight: 700; }
  .flap-rule {
    position: absolute; left: 0; top: 34px;
    width: 100%; height: 2px; background: var(--navy);
  }
  .brand-mark {
    position: absolute; right: 40px; top: 66px;
    display: flex; align-items: center; gap: 12px;
  }
  .brand-mark .dot {
    width: 40px; height: 40px; border-radius: 50%;
    border: 3px solid var(--navy); flex: none;
  }
  .brand-name {
    font-weight: 500; font-size: 34px; letter-spacing: 3px;
    color: var(--navy); line-height: 1;
  }
  .brand-tagline {
    font-size: 10px; letter-spacing: 7px; color: var(--ember);
    margin-top: 4px; font-weight: 500;
  }
  .scene-art {
    position: absolute; left: 40px; top: 120px;
    width: 340px; height: 210px;
    border-radius: 4px 4px 0 0;
    background: linear-gradient(180deg, #b9a88f 0%, #6f7580 50%, var(--navy) 100%);
  }
  .scent-rule {
    position: absolute; left: 380px; top: 160px;
    width: 380px; height: 5px; background: var(--navy);
  }
  .scent-name {
    position: absolute; left: 410px; top: 182px;
    font-weight: 800; font-size: 52px; line-height: 1.02;
    letter-spacing: 1px; color: var(--navy);
  }
  .info-band {
    position: absolute; left: 0; top: 330px;
    width: 760px; height: 40px;
    background: var(--navy); color: var(--cream);
    display: flex; align-items: center; justify-content: space-between;
    padding: 0 40px;
    font-weight: 600; font-size: 16px;
  }
  .info-band .weight strong { font-size: 20px; font-weight: 700; }
</style>
</head>
<body>
  <main class="box-layout">
    <section class="end-panel">
      <div class="end-brand">
        <span class="dot"></span>
        <div>
          <div class="brand-name">ROWAN HALE</div>
          <div class="brand-tagline">REAL SKINCARE</div>
        </div>
      </div>
    </section>
    <section class="top-panel">
      <div class="flap-rule"></div>
      <div class="brand-mark">
        <span class="dot"></span>
        <div>
          <div class="brand-name">ROWAN HALE</div>
          <div class="brand-tagline">REAL SKINCARE</div>
        </div>
      </div>
      <div class="scene-art" role="img" aria-label="Illustration of pine trees, a mountain under a setting sun, a lake and a man resting in a hammock by a campfire"></div>
      <div class="scent-rule"></div>
      <h1 class="scent-name">CINNAMON<br>BARK</h1>
      <div class="info-band">
        <span class="weight"><strong>5</strong> oz. bar</span>
        <span class="type">Men’s Natural Soap</span>
      </div>
    </section>
    <section class="front-panel">
      <p class="lead">Real Ingredients for Real Guys.</p>
      <p>Bring the outdoors in using real, natural ingredients on your skin. Traditional bar soap contains harsh chemical ingredients that can be harmful to you and the environment. Lather up with Rowan Hale’s handcrafted, all-natural soap and feel the difference.</p>
    </section>
  </main>
</body>
</html>
```